Brightline Energy Product Distribution Brochure

We are looking to have our current brochure for our customers completely redesigned...the idea is to present the relevant information in an attractive way . Our website is brightlineenergyco.example where you can find more information about us. We have included a file with a rough idea of the page order and what each should include but feel free to adapt based on design. The example provided is only for context and doesnt have to be maintained. We will be using the brochure both digitally and in print form. As long as it reads easily and is eye catching, the design can be horizontal or vertical.Final deliverable should be indesign file.

"Our Brands" page: should be limited to one page (space being enough) where it has the header for each one (for example diesel generators) space for one or two lines of text and then the corresponding logos for each of the five categories
Updates

For those asking: the "our brands" page should be a single page layout where there is a header with the corresponding section and space for maybe one line of text followed by the two logos for that category. Each of the product pages should be similar in fashion to the one in the document attached: a photo of the product with some white space and space for the text to be included. We will be posting additional examples today

Target Market(s)

We want to present it to customers both digitally and in print so they can see our products

Industry/Entity Type

Power Generation

Font styles to use
Serif

Requirements
Must have
• Eye catching and able to present the information in a presentable fashion. Rest is up to you.
Nice to have
• Should incorporate the colors of our logo but can also add other depending on design

```html
<!DOCTYPE html>
<html lang="en">
<head>
<meta charset="utf-8">
<title>Brightline Energy – Our Team / Our Brands</title>
<link rel="stylesheet" href="https://fonts.googleapis.com/css2?family=Michroma&family=Montserrat:wght@500;600;800&display=swap">
<style>
  :root{
    --stage:#e6e5e1;
    --paper:#ffffff;
    --paper-shade:#ecebee;
    --team-blue:#2f2d9a;
    --night:#2a2624;
    --night-light:#6b6560;
    --brand-yellow:#f2d11a;
    --diesel-blue:#3f3fb2;
    --alt-yellow:#f3c312;
    --controls-purple:#8f4cba;
    --switch-cyan:#3cb6dc;
    --ink:#2a2a2a;
    --muted:#9a9a9a;
  }
  *{box-sizing:border-box;margin:0;padding:0}
  html,body{width:1200px;height:960px;overflow:hidden;background:var(--stage)}
  .spread{
    position:absolute;left:40px;top:245px;width:1120px;height:470px;
    display:flex;box-shadow:0 18px 40px rgba(0,0,0,.18);
  }
  .page{position:relative;width:560px;height:470px;overflow:hidden}
  .page--team{
    background:linear-gradient(90deg,var(--paper-shade) 0%,var(--paper) 40%,var(--paper) 88%,#e4e3e8 100%);
    display:flex;align-items:center;justify-content:center;
  }
  .team-title{
    font-family:"Michroma",sans-serif;font-weight:400;font-size:52px;
    color:var(--team-blue);letter-spacing:-1px;
  }
  .page--brands{background:var(--night)}
  .brands-bg{position:absolute;inset:0}
  .brands-title{
    position:absolute;left:0;right:0;top:38px;text-align:center;
    font-family:"Michroma",sans-serif;font-size:22px;color:var(--brand-yellow);
    letter-spacing:1px;
  }
  .card{
    position:absolute;width:220px;background:var(--paper);
    box-shadow:0 6px 16px rgba(0,0,0,.35);
  }
  .card__head{
    font-family:"Montserrat",sans-serif;font-weight:800;font-size:11px;
    text-transform:uppercase;color:#fff;text-align:center;
    padding:8px 8px;line-height:1.1;letter-spacing:.3px;
  }
  .card--diesel{left:38px;top:130px}
  .card--diesel .card__head{background:var(--diesel-blue)}
  .card--alt{left:300px;top:112px}
  .card--alt .card__head{background:var(--alt-yellow)}
  .card--controls{left:58px;top:285px}
  .card--controls .card__head{background:var(--controls-purple)}
  .card--switch{left:318px;top:272px}
  .card--switch .card__head{background:var(--switch-cyan)}
  .card__logos{
    display:flex;justify-content:space-around;align-items:center;
    padding:12px 10px 6px;
  }
  .brand-name{
    display:flex;align-items:center;gap:5px;
    font-family:"Montserrat",sans-serif;font-weight:800;font-size:12px;
    color:var(--ink);text-transform:uppercase;
  }
  .brand-name__mark{width:10px;height:10px;background:var(--ink)}
  .card__text{
    font-family:"Montserrat",sans-serif;font-weight:500;font-size:6.5px;
    line-height:1.45;color:var(--muted);padding:4px 14px 12px;
  }
</style>
</head>
<body>
  <main class="spread">
    <section class="page page--team">
      <h1 class="team-title">OUR TEAM</h1>
    </section>

    <section class="page page--brands">
      <svg class="brands-bg" width="560" height="470" viewBox="0 0 560 470">
        <defs>
          <linearGradient id="plant" x1="0" y1="0" x2="1" y2="1">
            <stop offset="0" stop-color="#3a3532"/>
            <stop offset=".5" stop-color="#7b7570"/>
            <stop offset="1" stop-color="#2e2a28"/>
          </linearGradient>
        </defs>
        <rect width="560" height="470" fill="url(#plant)" role="img" aria-label="Black and white photograph of an industrial power plant with pipes and steel structures"/>
        <polygon points="0,0 120,0 560,470 440,470" fill="#ffffff" opacity=".12"/>
        <polygon points="330,0 560,0 560,190" fill="#1e1b1a" opacity=".75"/>
        <polygon points="0,0 230,0 0,160" fill="#1e1b1a" opacity=".55"/>
        <polygon points="0,330 0,470 170,470" fill="#1e1b1a" opacity=".45"/>
      </svg>

      <h2 class="brands-title">OUR BRANDS</h2>

      <article class="card card--diesel">
        <h3 class="card__head">Diesel Generators</h3>
        <div class="card__logos">
          <span class="brand-name"><span class="brand-name__mark"></span>Brightline Energy</span>
          <span class="brand-name">Halvorsen</span>
        </div>
        <p class="card__text">Reliable diesel units for standby and prime power, sized for sites large and small, backed by our team from quote to commissioning.</p>
      </article>

      <article class="card card--alt">
        <h3 class="card__head">AC Alternators/<br>Alternator Parts</h3>
        <div class="card__logos">
          <span class="brand-name">Ridgemoor</span>
          <span class="brand-name">Valcourt</span>
        </div>
        <p class="card__text">Alternators and spare parts for every common frame, in stock and ready to ship so your generator set stays online longer.</p>
      </article>

      <article class="card card--controls">
        <h3 class="card__head">Controls</h3>
        <div class="card__logos">
          <span class="brand-name"><span class="brand-name__mark"></span>Tessaline</span>
          <span class="brand-name">Corvane</span>
        </div>
        <p class="card__text">Control modules that start, monitor and protect each set, with clear panels and remote access for quick checks from anywhere on site.</p>
      </article>

      <article class="card card--switch">
        <h3 class="card__head">Transfer Switches</h3>
        <div class="card__logos">
          <span class="brand-name">Northgate</span>
          <span class="brand-name">Ardent</span>
        </div>
        <p class="card__text">Automatic and manual switches that move loads between utility and generator power smoothly, keeping critical systems running through every outage.</p>
      </article>
    </section>
  </main>
</body>
</html>
```